General contractor/GM consaltant business card

I need a card for my contracting company in North Dakota, we build industrial buildings for the oil feild and oil feild related companies offices, shops, airplain hangars, airports ext. We have a familly atmosphere on the job and are very relational and personal.
Industry/Entity Type
Industrial
Contact Information for Business Card
Ridgepost Contractors LLC.
Derek T.Holloway
4837 Tamarind dr. Colorado Springs, CO. 80917
Cell# 406-555-0148
derek@ridgepostcontractors.com

```html
<!DOCTYPE html>
<html lang="en">
<head>
<meta charset="utf-8">
<title>Ridgepost Contractors LLC. – Business Card</title>
<link rel="stylesheet" href="https://fonts.googleapis.com/css2?family=Crimson+Text:wght@700&family=Arimo:wght@400&display=swap">
<style>
  :root {
    --backdrop: #3b3536;
    --paper: #f7f7f6;
    --brand-red: #d0232f;
    --brand-blue: #2456a6;
    --ink-blue: #2b4f9a;
  }
  * { margin: 0; padding: 0; box-sizing: border-box; }
  html, body { width: 1200px; height: 858px; overflow: hidden; }
  body {
    background: var(--backdrop);
    position: relative;
    font-family: "Arimo", Arial, sans-serif;
  }
  .card {
    position: absolute;
    top: 274px;
    width: 540px;
    height: 309px;
    background: var(--paper);
    overflow: hidden;
    box-shadow: 0 10px 30px rgba(0,0,0,.45);
  }
  .card--front { left: 40px; }
  .card--back { left: 620px; }

  /* front */
  .side-band { position: absolute; left: 0; top: 0; bottom: 0; width: 32px; background: var(--brand-red); }
  .side-rule { position: absolute; left: 37px; top: 0; bottom: 0; width: 4px; background: var(--brand-blue); }
  .corner-tab { position: absolute; right: 0; top: 0; width: 30px; height: 58px; background: var(--brand-red); }
  .corner-rule { position: absolute; right: 34px; top: 0; width: 4px; height: 58px; background: var(--brand-blue); }
  .company-name {
    font-family: "Crimson Text", Georgia, serif;
    font-weight: 700;
    color: var(--brand-red);
    white-space: nowrap;
  }
  .card--front .company-name { position: absolute; left: 52px; top: 84px; font-size: 33px; }
  .person-name {
    position: absolute; right: 64px; top: 148px;
    font-size: 19px; color: var(--brand-red);
  }
  .contact-list { position: absolute; left: 64px; top: 190px; list-style: none; }
  .contact-list li {
    display: flex; align-items: center; gap: 10px;
    font-size: 14.5px; color: var(--ink-blue);
    height: 26px;
  }
  .contact-list svg { width: 14px; height: 14px; flex: none; fill: var(--brand-red); }

  /* back */
  .card--back .company-name {
    position: absolute; left: 0; right: 0; top: 92px;
    text-align: center; font-size: 40px;
  }
  .base-stripe--blue { position: absolute; left: 0; right: 0; bottom: 40px; height: 20px; background: var(--brand-blue); }
  .base-stripe--red { position: absolute; left: 0; right: 0; bottom: 0; height: 30px; background: var(--brand-red); }
</style>
</head>
<body>
  <section class="card card--front">
    <div class="side-band"></div>
    <div class="side-rule"></div>
    <div class="corner-rule"></div>
    <div class="corner-tab"></div>
    <h1 class="company-name">Ridgepost Contractors LLC.</h1>
    <p class="person-name">Derek T.Holloway</p>
    <ul class="contact-list">
      <li>
        <svg viewBox="0 0 16 16" aria-hidden="true"><path d="M3 1h3l1.5 4-2 1.3a9 9 0 0 0 4.2 4.2L11 8.5l4 1.5v3a2 2 0 0 1-2 2A12 12 0 0 1 1 3a2 2 0 0 1 2-2z"/></svg>
        406-555-0148
      </li>
      <li>
        <svg viewBox="0 0 16 16" aria-hidden="true"><path d="M8 0a5.5 5.5 0 0 0-5.5 5.5C2.5 10 8 16 8 16s5.5-6 5.5-10.5A5.5 5.5 0 0 0 8 0zm0 8a2.5 2.5 0 1 1 0-5 2.5 2.5 0 0 1 0 5z"/></svg>
        4837 Tamarind dr. Colorado Springs, CO. 80917
      </li>
      <li>
        <svg viewBox="0 0 16 16" aria-hidden="true"><path d="M0 3h16v10H0zM1.5 4.5v.4L8 9.3l6.5-4.4v-.4z" fill-rule="evenodd"/></svg>
        derek@ridgepostcontractors.com
      </li>
    </ul>
  </section>

  <section class="card card--back">
    <h2 class="company-name">Ridgepost Contractors LLC.</h2>
    <div class="base-stripe--blue"></div>
    <div class="base-stripe--red"></div>
  </section>
</body>
</html>
```